Commercial Real Estate

We need a business card design for a new commercial real estate business that specializes in apartment building brokerage. Not individual units but the entire complex. We find and represent the owners existing buildings and well as new buyers for those buildings. The design should convey trust, integrity, knowledge and growth. It should be easily read.

Target Market(s)

40 to 65 years old

Industry/Entity Type

Real Estate

```html
<!DOCTYPE html>
<html lang="en">
<head>
<meta charset="utf-8">
<title>Stonebridge Property Investments – Business Card</title>
<link href="https://fonts.googleapis.com/css2?family=Open+Sans:wght@400;600;700&display=swap" rel="stylesheet">
<style>
  :root {
    --page-bg: #e4e5e6;
    --card-bg: #ffffff;
    --card-edge: #f1f2f3;
    --teal: #5cbfbf;
    --teal-deep: #4aa9aa;
    --slate: #59636a;
    --ink: #2f3539;
    --window-grey: #636b70;
  }
  * { margin: 0; padding: 0; box-sizing: border-box; }
  html, body {
    width: 1038px;
    height: 1200px;
    overflow: hidden;
  }
  body {
    background: var(--page-bg);
    font-family: "Open Sans", Arial, sans-serif;
    color: var(--ink);
    position: relative;
  }
  .card {
    position: absolute;
    left: 89px;
    width: 860px;
    height: 490px;
    background: linear-gradient(160deg, var(--card-bg) 0%, var(--card-bg) 55%, var(--card-edge) 100%);
    box-shadow: 0 6px 14px rgba(0, 0, 0, 0.22);
    overflow: hidden;
  }
  .card--front { top: 90px; }
  .card--back { top: 640px; }

  .tower-art {
    position: absolute;
    left: 30px;
    top: 0;
    width: 330px;
    height: 490px;
  }

  .card-info {
    position: absolute;
    left: 453px;
    top: 66px;
  }
  .brand-name {
    font-weight: 600;
    font-size: 40px;
    letter-spacing: 1px;
    color: var(--slate);
    line-height: 1;
  }
  .brand-rule {
    width: 232px;
    height: 2px;
    background: var(--slate);
    margin: 10px 0 5px;
  }
  .brand-tagline {
    font-weight: 700;
    font-size: 15px;
    letter-spacing: 2.4px;
    color: var(--slate);
  }
  .person-name {
    margin-top: 72px;
    font-weight: 600;
    font-size: 23px;
    color: var(--teal);
  }
  .person-title {
    font-size: 20px;
    color: var(--ink);
    margin-top: 2px;
  }
  .contact-list {
    list-style: none;
    margin-top: 34px;
  }
  .contact-item {
    display: flex;
    align-items: center;
    font-size: 19px;
    line-height: 33px;
    color: var(--ink);
  }
  .contact-icon {
    width: 16px;
    height: 16px;
    margin-right: 14px;
    fill: var(--teal);
    flex: none;
  }
  .contact-address {
    font-size: 19px;
    line-height: 33px;
    margin-top: 2px;
  }
</style>
</head>
<body>

  <section class="card card--front" aria-label="Business card front">
    <svg class="tower-art" viewBox="0 0 330 490" role="img" aria-label="Illustration of a teal apartment tower seen in upward perspective">
      <defs>
        <linearGradient id="towerTone" x1="0" y1="0" x2="0" y2="1">
          <stop offset="0" stop-color="#5cbfbf"/>
          <stop offset="1" stop-color="#7fcfcf"/>
        </linearGradient>
      </defs>
      <rect x="0" y="0" width="330" height="490" fill="url(#towerTone)"/>
    </svg>

    <div class="card-info">
      <div class="brand-name">STONEBRIDGE</div>
      <div class="brand-rule"></div>
      <div class="brand-tagline">Property Investments</div>

      <div class="person-name">Daniel Harrow</div>
      <div class="person-title">Technical Director</div>

      <ul class="contact-list">
        <li class="contact-item">
          <svg class="contact-icon" viewBox="0 0 16 16" aria-hidden="true"><path d="M3.2 1.5l2.4 0 1 3.4-1.6 1.2c.8 1.8 2.1 3.1 3.9 3.9l1.2-1.6 3.4 1v2.4c0 .8-.7 1.4-1.5 1.4C6.7 13.2 2.8 9.3 1.8 3c0-.8.6-1.5 1.4-1.5z"/></svg>
          03 5550 1234
        </li>
        <li class="contact-item">
          <svg class="contact-icon" viewBox="0 0 16 16" aria-hidden="true"><path d="M4.5 1h7a1 1 0 0 1 1 1v12a1 1 0 0 1-1 1h-7a1 1 0 0 1-1-1V2a1 1 0 0 1 1-1zm.6 2v8.6h5.8V3zM8 12.4a.8.8 0 1 0 0 1.6.8.8 0 0 0 0-1.6z"/></svg>
          0400 555 019
        </li>
        <li class="contact-item">
          <svg class="contact-icon" viewBox="0 0 16 16" aria-hidden="true"><path d="M1 4h14v9H1zm1.6 1.2L8 9l5.4-3.8V5H2.6z"/></svg>
          daniel@harrowgroup.com.au
        </li>
        <li class="contact-item">
          <svg class="contact-icon" viewBox="0 0 16 16" aria-hidden="true"><path d="M8 1a7 7 0 1 0 0 14A7 7 0 0 0 8 1zm0 1.4c.7.8 1.3 2 1.5 3.3h-3C6.7 4.4 7.3 3.2 8 2.4zM2.6 9.3a5.6 5.6 0 0 1 0-2.6h2.5a11 11 0 0 0 0 2.6zm.5 1.3h2.2c.2 1 .6 1.9 1 2.7a5.6 5.6 0 0 1-3.2-2.7zm2.2-4.9H3.1a5.6 5.6 0 0 1 3.2-2.7c-.4.8-.8 1.7-1 2.7zM8 13.6c-.7-.8-1.3-2-1.5-3h3c-.2 1-.8 2.2-1.5 3zm1.7-4.3H6.3a9.5 9.5 0 0 1 0-2.6h3.4a9.5 9.5 0 0 1 0 2.6zm0 4a9 9 0 0 0 1-2.7h2.2a5.6 5.6 0 0 1-3.2 2.7zm1.2-4a11 11 0 0 0 0-2.6h2.5a5.6 5.6 0 0 1 0 2.6zm-.2-3.9c-.2-1-.6-1.9-1-2.7a5.6 5.6 0 0 1 3.2 2.7z"/></svg>
          www.stonebridge.com.au
        </li>
      </ul>
      <div class="contact-address">Level 2, 18 Keller St, Australia Sydney</div>
    </div>
  </section>

  <section class="card card--back" aria-label="Business card back"></section>

</body>
</html>
```